Envelope Design - Winner can do follow-up business

- Varnoko.com is a Swiss-based online store selling business shirts and accessories for business men
- Please visit the webpage to make yourself familiar with the company. Although the text is in German, with Plimbo translator you should be able to understand the main content.
- Our clients are mainly business men between 30 and 60 years old. Mostly with a high income working in the service industry (banking, insurance, lawyers, etc.). Sometimes there wives purchase the shirts for them ;-)
- The colors and the logo are given, as they are also used for the print materials (please see files in attachment)
- I am running several businesses and often need a talented web designer --> the winner gets substantial follow-up business
your task:
-for our company we need a new envelope design
-It should be simple and modern
-please use one of the logos in the followings.
-suprise me :)

```html
<!DOCTYPE html>
<html lang="en">
<head>
<meta charset="utf-8">
<title>Varnoko Envelope Set</title>
<link rel="stylesheet" href="https://fonts.googleapis.com/css2?family=Michroma&family=Open+Sans:wght@400&display=swap">
<style>
:root{
  --backdrop:#4a2e1b;
  --paper:#ffffff;
  --edge:#8c8c8c;
  --peach:#f9c1a8;
  --peach-soft:#fbd6c6;
  --cream:#fdf3d2;
  --sand:#fde6c2;
  --sand-light:#fdf3d8;
  --ink:#111111;
  --gold:#e0cf5a;
  --accent:#e8392b;
  --text:#222222;
}
*{margin:0;padding:0;box-sizing:border-box}
html,body{width:1200px;height:1011px;overflow:hidden}
body{background:var(--backdrop);position:relative;font-family:"Open Sans",Arial,sans-serif}
.envelope{position:absolute;width:974px;height:458px;background:var(--paper);border:1px solid var(--edge);overflow:hidden}
.envelope--back-rear{left:113px;top:92px;height:420px}
.envelope--back-front{left:34px;top:277px}
.envelope--front{left:188px;top:500px}
.flap{position:absolute;left:0;top:0;width:974px;height:160px}
.wordmark{position:absolute;font-family:"Michroma",Arial,sans-serif;letter-spacing:1px;white-space:nowrap;transform:translateX(-50%)}
.wordmark--flap{font-size:26px;color:var(--ink)}
.envelope--back-rear .wordmark{left:477px;top:80px}
.envelope--back-front .wordmark{left:477px;top:84px}
.pattern-panel{position:absolute;left:0;top:0;width:380px;height:458px}
.wordmark--front{left:320px;top:242px;font-size:40px;color:var(--gold)}
.web{position:absolute;left:12px;top:352px;text-align:center;font-size:18px;color:var(--text)}
.web svg{display:block;margin:0 auto 2px}
.address{position:absolute;right:26px;top:420px;display:flex;align-items:center;gap:12px;font-size:19px;color:var(--text)}
</style>
</head>
<body>

<section class="envelope envelope--back-rear" aria-label="Envelope back, rear">
  <svg class="flap" viewBox="0 0 974 160" role="img" aria-label="Flap with peach and cream diamond pattern">
    <defs>
      <linearGradient id="flapA" x1="0" x2="1" y1="0" y2="0">
        <stop offset="0" stop-color="var(--cream)"/>
        <stop offset="0.5" stop-color="var(--peach)"/>
        <stop offset="1" stop-color="var(--cream)"/>
      </linearGradient>
    </defs>
    <path d="M0 0H974L962 36Q952 66 915 74L520 148Q477 156 434 148L60 76Q22 68 12 40Z" fill="url(#flapA)"/>
  </svg>
  <div class="wordmark wordmark--flap">VARNOKO</div>
</section>

<section class="envelope envelope--back-front" aria-label="Envelope back, front">
  <svg class="flap" viewBox="0 0 974 160" role="img" aria-label="Flap with soft peach and cream diamond pattern">
    <defs>
      <linearGradient id="flapB" x1="0" x2="1" y1="0" y2="0">
        <stop offset="0" stop-color="var(--cream)"/>
        <stop offset="0.5" stop-color="var(--peach-soft)"/>
        <stop offset="1" stop-color="var(--cream)"/>
      </linearGradient>
    </defs>
    <path d="M0 0H974L962 40Q952 72 915 80L520 150Q477 158 434 150L60 82Q22 74 12 44Z" fill="url(#flapB)"/>
  </svg>
  <div class="wordmark wordmark--flap">VARNOKO</div>
</section>

<section class="envelope envelope--front" aria-label="Envelope front">
  <svg class="pattern-panel" viewBox="0 0 380 458" role="img" aria-label="Sand and cream diamond pattern panel">
    <defs>
      <linearGradient id="panel" x1="0" x2="1" y1="0" y2="1">
        <stop offset="0" stop-color="var(--sand-light)"/>
        <stop offset="0.5" stop-color="var(--sand)"/>
        <stop offset="1" stop-color="var(--sand-light)"/>
      </linearGradient>
    </defs>
    <path d="M0 0H372L137 245L347 458H0Z" fill="url(#panel)"/>
  </svg>
  <div class="wordmark wordmark--front">VARNOKO</div>
  <div class="web">
    <svg width="24" height="24" viewBox="0 0 24 24" fill="none" stroke="var(--accent)" stroke-width="1.5" aria-hidden="true">
      <circle cx="12" cy="12" r="10"/><ellipse cx="12" cy="12" rx="4.5" ry="10"/>
      <path d="M2 12H22M4 6.5H20M4 17.5H20"/>
    </svg>
    varnoko.com
  </div>
  <div class="address">
    <svg width="18" height="26" viewBox="0 0 18 26" aria-hidden="true">
      <path d="M9 0C4 0 0 4 0 9c0 6.5 9 17 9 17s9-10.5 9-17C18 4 14 0 9 0z" fill="var(--accent)"/>
      <circle cx="9" cy="9" r="3.4" fill="var(--paper)"/>
    </svg>
    <span>Street Name, City Name, State Zipcode</span>
  </div>
</section>

</body>
</html>
```